MyName is TapLedger .... Killer of Business Cards!!! WANT a KickAss Design Landing Page :)

How 'TapLedger' works:
- with a unique name for each country, like a personalise car plate number
- our platform links through a 'Quick Text' keyword short code
- TapLedger platform will respond with downloaded ready full contact business file link
- this is designed to be downloaded in just '3 clicks' into your Contacts Folder
- any changes,,updates, images, online profiles can be made in real time updates
- TapLedger provides a backend login to manage individual account and is ready
Enterprise model for larger staff companies
- platform is international ready and have launched
Australia, in September 2019.

Yes, your whole business card and online profile in '3' simple clicks. No '20-30 mins' of typing the business card contacts details into mobile phones.
** Fact: 88% of business cards are lost of thrown out within 7 days.
(https://www.plumfinchstats.com/business-card-statistics.html) **

NZ ClipStream
https://vidhost.example/q7Rt2LmP9xZ

**current websites are www.tapledge.co.nz www.taplink.com.au www.tapledgerau.com www.tapledgerus.com **

Target Market(s)

Anybody who uses a business card, from trades person, real estate agents, consultants, bankers (in NZ/AU with have plumbers, financial advisors, real estate agents, mortgage brokers, sports agents, Telcos etc etc)

Industry/Entity Type

Business Software

Coding

Coded - Design and coding required

Number of Pages Required

4 page

Font styles to use
Other font styles liked:
• libre franklin black

Requirements
Must have
• TapLedger a simple 'in delivery' and smart 'in innovation' solution so our message is Simple, Clear and Inquisitive. We would like a converting landing page because we are selling Nimble Cloud Suite at low-entry cost and no-contract. IWe want to direct clients to a name reservation platform to a virtual business card that uses our Nimble Core Engine. We will require some code at the back to link the name reservation and sign up source code(javascript). This web/landing page fresh page is required because we have recently changed our marketing strategy to be purely digital marketing in Chatterbook and Snapgrid Ads from now on. We would like this to be exciting graphically to grab attention, inquisitive enough to check your name availability and follow through with call to action with the right colours and graphics images. We plan to test the right pitch offering until we get the markets feedback on the best offering/re-design and then push harder with more CB and SG Ads. ( **we plan to continue multiple regular campaigns as the business has now change our strategy due to covid-19 and we will focus mainly on direct to consumers**)

Also:
2 buttons: Signup and a Check availability little form to allow a java script to be added/HTML5/CB advertising/Super Inviting to check 'YOUR UNIQUE NAME' is available. Then clicking the to reserve the name to purchase our Quick Text/Eco-Friendly/Relevant to todays tech and Low Cost service. We will be offering Promo codes for each campaign.
No Apps. Works with SMS, any smartphone, country specific, enterprise ready, and CONTACTLESS ....
Nice to have
• Personal feeling. Unique choice of 'your name' as this is your business and social profile in one. Strong independent images and confident to share with anybody their profile by just sharing their name.
Should not have
• Open currently....

```html
<!DOCTYPE html>
<html lang="en">
<head>
<meta charset="utf-8">
<title>TapLedger – Share Your Business Contact Details</title>
<link href="https://fonts.googleapis.com/css2?family=Libre+Franklin:wght@600;700;800;900&family=Lato:wght@400;700&display=swap" rel="stylesheet">
<style>
:root{
  --teal:#1d6f78;
  --teal-dark:#175b63;
  --navy:#1b2465;
  --ink:#1f2833;
  --text:#3d4550;
  --muted:#6b7280;
  --tint:#f5f7fc;
  --grey:#f4f4f4;
  --line:#d9dde3;
  --footer:#2b2b2b;
  --white:#ffffff;
}
*{box-sizing:border-box;margin:0;padding:0}
html,body{width:1200px;height:4835px;overflow:hidden}
body{position:relative;background:var(--white);font-family:'Lato',sans-serif;color:var(--text)}
.backdrop{position:absolute;left:0;top:0;width:1200px;height:4835px}
.abs{position:absolute}
h1,h2,h3,.brand,.nav,.btn{font-family:'Libre Franklin',sans-serif}

/* header */
.brand{left:75px;top:40px;display:flex;align-items:center;gap:12px;font-weight:800;font-size:28px;color:var(--teal)}
.brand-dot{width:38px;height:38px;border-radius:50%;background:var(--teal)}
.nav{left:475px;top:55px;display:flex;align-items:center;font-size:13px;font-weight:700;color:var(--white);letter-spacing:.2px}
.nav a{color:inherit;text-decoration:none;margin-right:34px}
.nav a.active{color:#5fc3cc;border-bottom:2px solid #5fc3cc;padding-bottom:8px;margin-top:10px}
.nav .signup{background:var(--teal);border-radius:22px;padding:12px 20px;margin-right:0;margin-left:-6px}

/* hero */
.hero-title{left:75px;top:258px;font-size:35px;line-height:41px;font-weight:800;color:var(--ink)}
.hero-title span{color:var(--teal)}
.ticks{left:75px;top:405px;list-style:none;font-size:16px;color:var(--text)}
.ticks li{display:flex;align-items:center;height:38px}
.ticks svg{margin-right:18px;flex:none}
.reserve-note{left:75px;top:574px;font-size:16px}
.field{border:1.5px solid var(--line);border-radius:30px;background:var(--white);font-size:18px;color:#444;display:flex;align-items:center;padding-left:26px}
.btn{display:flex;align-items:center;justify-content:center;border-radius:30px;font-weight:700;text-decoration:none}
.btn-outline{border:2px solid var(--teal);color:var(--teal);background:transparent}
.btn-solid{background:var(--teal);color:var(--white)}
.btn-light{border:2px solid var(--white);color:var(--white)}

/* section titles */
.section-title{left:0;width:1200px;text-align:center;font-size:41px;font-weight:700;color:var(--ink)}
.section-title.light{color:var(--white)}

/* benefits */
.benefit{width:512px;height:146px;background:var(--white);border-radius:6px;display:flex;padding:24px 20px}
.benefit.raised{box-shadow:0 3px 14px rgba(0,0,0,.16)}
.benefit-icon{width:100px;height:96px;flex:none;border-radius:14px;background:#e9e9e9;transform:rotate(-4deg);display:flex;align-items:center;justify-content:center;margin-right:32px}
.benefit-icon svg{transform:rotate(4deg)}
.benefit h3{font-size:23px;font-weight:700;color:var(--navy);margin:5px 0 10px}
.benefit p{font-size:14.5px;line-height:25px;color:var(--text)}

/* partners */
.partners-title{left:75px;top:1830px;font-size:41px;font-weight:700;color:var(--ink)}
.partners-copy{left:75px;top:1896px;width:540px;font-size:16.5px;line-height:32.5px;color:var(--text);white-space:nowrap}
.partner-mark{left:75px;top:2148px;display:flex;align-items:center;gap:10px;font-family:'Libre Franklin',sans-serif;font-weight:700;font-size:34px;color:var(--teal)}
.partner-mark i{width:64px;height:64px;border-radius:50%;background:var(--teal);display:block}
.scene{left:630px;top:1840px;width:545px;height:432px;border-radius:48% 52% 40% 60%/55% 45% 55% 45%;background:linear-gradient(150deg,#e9eefb 0%,#d4ddf4 60%,#c9d3ee 100%)}

/* promo */
.promo-card{left:165px;top:2547px;width:872px;height:161px;background:var(--white);border-radius:8px;text-align:center;padding:36px 40px 0}
.promo-card p{font-size:15px;line-height:25px;color:var(--text)}
.promo-code{margin-top:14px;font-size:13.5px;color:var(--teal);letter-spacing:.3px}
.promo-code b{font-family:'Libre Franklin',sans-serif;font-size:19px;color:var(--navy);font-weight:700}
.arrow{width:30px;height:46px}

/* plans */
.plan{width:332px;height:406px;background:var(--white);box-shadow:0 2px 14px rgba(0,0,0,.12);text-align:center}
.price{position:absolute;left:97px;top:36px;width:141px;height:129px;border-radius:18px;background:linear-gradient(160deg,var(--navy) 0%,#134f67 100%);transform:rotate(-3deg);color:var(--white);display:flex;flex-direction:column;align-items:center;justify-content:center}
.price strong{font-family:'Libre Franklin',sans-serif;font-size:36px;font-weight:700;line-height:38px}
.price strong sup{font-size:18px;vertical-align:top;position:relative;top:4px}
.price small{font-size:14.5px;font-weight:700}
.plan h3{position:absolute;left:0;width:100%;top:196px;font-size:23px;font-weight:700;color:var(--navy)}
.plan p{position:absolute;left:26px;right:26px;top:236px;font-size:16.5px;line-height:28px}
.plan .btn{position:absolute;left:78px;top:312px;width:177px;height:56px;font-size:16px}

/* testimonials */
.quote-card{left:165px;top:3662px;width:872px;height:272px;background:var(--white);border-radius:8px;text-align:center;padding:30px 34px 0}
.quote-card p{font-size:14.5px;line-height:30.5px;color:var(--text);position:relative}
.quote-card h3{margin-top:12px;font-size:19px;font-weight:700;color:var(--navy)}
.quote-card .role{font-size:14.5px;color:var(--teal);margin-top:4px}
.qmark{font-family:Georgia,serif;font-size:130px;line-height:1;color:#e3e3e3}

/* subscribe */
.subscribe-copy{left:0;width:1200px;top:4248px;text-align:center;font-size:17px}

/* footer */
.footer-brand{left:75px;top:4590px;display:flex;align-items:center;gap:12px;font-family:'Libre Franklin',sans-serif;font-weight:800;font-size:28px;color:#cfcfcf}
.footer-brand i{width:38px;height:38px;border-radius:50%;background:#cfcfcf;display:block}
.fine{font-size:12px;line-height:22px;color:#d6d6d6}
.foot-col h4{font-family:'Libre Franklin',sans-serif;font-size:17px;font-weight:700;color:var(--white);margin-bottom:10px}
.foot-col ul{list-style:none}
.foot-col li{font-size:13.5px;line-height:28px;color:#d6d6d6}
.foot-col p{font-size:13.5px;line-height:26px;color:#d6d6d6}
.socials{display:flex;gap:14px;font-size:13px;font-weight:700;color:var(--white)}
.cards{display:flex;gap:10px}
.cards span{width:36px;height:23px;border-radius:4px;background:#e4e4e4;display:block}
</style>
</head>
<body>

<svg class="backdrop" viewBox="0 0 1200 4835">
  <rect x="0" y="0" width="1200" height="415" fill="var(--tint)"/>
  <defs>
    <linearGradient id="photoTone" x1="0" y1="0" x2="1" y2="1">
      <stop offset="0" stop-color="#4a4340"/>
      <stop offset=".55" stop-color="#2a2624"/>
      <stop offset="1" stop-color="#1a1816"/>
    </linearGradient>
  </defs>
  <g role="img" aria-label="Photo of a hand holding a smartphone showing a TapLedger contact card">
    <path d="M423,0 C440,160 560,300 720,400 C860,490 900,660 1080,668 C1150,670 1190,630 1200,610 L1200,0 Z" fill="url(#photoTone)"/>
  </g>
  <path d="M0,920 C250,800 420,700 700,760 C900,800 1050,760 1200,730 L1200,1615 C1000,1650 700,1640 400,1690 C200,1720 80,1760 0,1785 Z" fill="var(--grey)"/>
  <path d="M0,2442 C200,2400 350,2330 600,2330 C850,2330 1050,2300 1200,2245 L1200,2870 L0,2870 Z" fill="var(--navy)"/>
  <rect x="0" y="2870" width="1200" height="651" fill="var(--tint)"/>
  <path d="M0,3521 L1200,3521 L1200,4000 C1000,4040 700,4020 400,4080 C220,4110 80,4140 0,4160 Z" fill="var(--navy)"/>
  <path d="M0,4507 C300,4470 700,4460 1000,4420 C1100,4405 1160,4395 1200,4390 L1200,4835 L0,4835 Z" fill="var(--footer)"/>
</svg>

<!-- header -->
<div class="abs brand"><span class="brand-dot"></span>TapLedger</div>
<nav class="abs nav">
  <a class="active" href="#">HOME</a><a href="#">PARTNERS</a><a href="#">BENEFITS</a><a href="#">PLANS</a><a href="#">TESTIMONIALS</a><a href="#">LOG IN</a><a class="signup" href="#">SIGN UP</a>
</nav>

<!-- hero -->
<h1 class="abs hero-title">Instantly Share All<br>Your Business Contact<br>Details with <span>1 ‘QUICK’ TEXT</span></h1>
<ul class="abs ticks">
  <li><svg width="16" height="16" viewBox="0 0 16 16"><circle cx="8" cy="8" r="8" fill="var(--teal)"/><path d="M4.5 8.2l2.3 2.3 4.7-4.7" stroke="#fff" stroke-width="2" fill="none"/></svg>No more business cards, that’s so unique and cool.</li>
  <li><svg width="16" height="16" viewBox="0 0 16 16"><circle cx="8" cy="8" r="8" fill="var(--teal)"/><path d="M4.5 8.2l2.3 2.3 4.7-4.7" stroke="#fff" stroke-width="2" fill="none"/></svg>Try it now. Txt ‘TapLedger’ to 420 555 010</li>
  <li><svg width="16" height="16" viewBox="0 0 16 16"><circle cx="8" cy="8" r="8" fill="var(--teal)"/><path d="M4.5 8.2l2.3 2.3 4.7-4.7" stroke="#fff" stroke-width="2" fill="none"/></svg>Pretty cool right... Get Your Quick Text code instantly.</li>
  <li><svg width="16" height="16" viewBox="0 0 16 16"><circle cx="8" cy="8" r="8" fill="var(--teal)"/><path d="M4.5 8.2l2.3 2.3 4.7-4.7" stroke="#fff" stroke-width="2" fill="none"/></svg>TapLedger - Simple, Low Cost, Smart and Effective!</li>
</ul>
<p class="abs reserve-note">Click below to reserve.</p>
<div class="abs field" style="left:75px;top:629px;width:380px;height:57px">Enter Keyword</div>
<a class="abs btn btn-outline" href="#" style="left:468px;top:629px;width:242px;height:57px;font-size:16px">CHECK AVAILABILITY</a>

<!-- benefits -->
<h2 class="abs section-title" style="top:896px">Simple Benefits Are</h2>

<div class="abs benefit raised" style="left:75px;top:1005px">
  <div class="benefit-icon"><svg width="46" height="40" viewBox="0 0 46 40"><circle cx="16" cy="22" r="10" fill="none" stroke="var(--teal)" stroke-width="7" stroke-dasharray="4 3"/><circle cx="16" cy="22" r="4" fill="var(--teal)"/><circle cx="36" cy="10" r="6" fill="none" stroke="var(--teal)" stroke-width="5" stroke-dasharray="3 2"/><circle cx="36" cy="30" r="5" fill="none" stroke="var(--teal)" stroke-width="4" stroke-dasharray="3 2"/></svg></div>
  <div><h3>Logical</h3><p>Everybody has a mobile phone and every<br>phone can txt/sms.</p></div>
</div>
<div class="abs benefit" style="left:614px;top:1005px">
  <div class="benefit-icon"><svg width="46" height="38" viewBox="0 0 46 38"><circle cx="23" cy="10" r="7" fill="var(--teal)"/><circle cx="9" cy="14" r="5" fill="var(--teal)"/><circle cx="37" cy="14" r="5" fill="var(--teal)"/><path d="M11 36c0-9 5-15 12-15s12 6 12 15z" fill="var(--teal)"/><path d="M0 34c0-7 4-12 9-12 3 0 5 1 6 3-2 3-3 6-3 9z" fill="var(--teal)"/><path d="M46 34c0-7-4-12-9-12-3 0-5 1-6 3 2 3 3 6 3 9z" fill="var(--teal)"/></svg></div>
  <div><h3>Professional</h3><p>Your customers / potential customers will be<br>impressed with your innovation.</p></div>
</div>
<div class="abs benefit" style="left:75px;top:1178px">
  <div class="benefit-icon"><svg width="30" height="36" viewBox="0 0 30 36"><path d="M7 16v-6a8 8 0 0116 0v6" fill="none" stroke="var(--teal)" stroke-width="4"/><rect x="2" y="15" width="26" height="20" rx="3" fill="var(--teal)"/></svg></div>
  <div><h3>Data Safe</h3><p>All data is held on a secure Skyvault Hosting<br>infrastructure in Sydney, which puts strong<br>safeguards in place to protect.</p></div>
</div>
<div class="abs benefit" style="left:614px;top:1178px">
  <div class="benefit-icon"><svg width="46" height="30" viewBox="0 0 46 30"><rect x="2" y="2" width="42" height="26" rx="2" fill="none" stroke="var(--teal)" stroke-width="4"/><circle cx="23" cy="15" r="7" fill="var(--teal)"/><rect x="8" y="8" width="4" height="14" fill="var(--teal)"/><rect x="34" y="8" width="4" height="14" fill="var(--teal)"/></svg></div>
  <div><h3>Secure Payment</h3><p>Back by the global Coinrelay payment gateway.<br>Coinrelay a certified as a PCI Level One Service<br>Provider.</p></div>
</div>
<div class="abs benefit" style="left:75px;top:1350px">
  <div class="benefit-icon"><svg width="44" height="38" viewBox="0 0 44 38"><path d="M6 34C6 14 20 4 42 4 42 24 30 34 12 32z" fill="none" stroke="var(--teal)" stroke-width="4"/><path d="M4 36L30 14" stroke="var(--teal)" stroke-width="4"/></svg></div>
  <div><h3>Environment</h3><p>No use of business cards, you no longer need to<br>have cards printed, thus reducing your<br>carbon foot print.</p></div>
</div>
<div class="abs benefit" style="left:614px;top:1350px">
  <div class="benefit-icon"><svg width="44" height="38" viewBox="0 0 44 38"><path d="M3 2v33h39" fill="none" stroke="var(--teal)" stroke-width="3"/><rect x="9" y="20" width="5" height="12" fill="var(--teal)"/><rect x="17" y="12" width="5" height="20" fill="var(--teal)"/><rect x="25" y="16" width="5" height="16" fill="var(--teal)"/><rect x="33" y="8" width="5" height="24" fill="var(--teal)"/></svg></div>
  <div><h3>Sales</h3><p>May increase your sales by word of mouth,<br>added to your advertising and ability to share<br>TapLedger anywhere, anytime.</p></div>
</div>
<a class="abs btn btn-outline" href="#" style="left:488px;top:1548px;width:224px;height:56px;font-size:16px">VIEW ALL BENEFITS</a>

<!-- partners -->
<h2 class="abs partners-title">Our Partners</h2>
<p class="abs partners-copy">Reclaimo™ is the World’s Largest Global Recovery company<br>which helps return lost items to their rightful owners.<br>With over an 80% recovery rate, Reclaimo recovery tags help<br>identify and protect all types of portable items ranging from<br>cell phones to laptops, keys to luggage and even cats &amp; dogs.<br>Reclaimo’s system is simple, convenient, confidential<br>and rewarding!</p>
<div class="abs partner-mark"><i></i>Reclaimo</div>
<div class="abs scene" role="img" aria-label="Illustration of two business people shaking hands at a reception desk"></div>

<!-- promo codes -->
<h2 class="abs section-title light" style="top:2462px">Promo Codes</h2>
<svg class="abs arrow" style="left:98px;top:2603px" viewBox="0 0 30 46"><path d="M24 4L6 23l18 19" fill="none" stroke="#c9cde0" stroke-width="5"/></svg>
<div class="abs promo-card">
  <p>Quisque faucibus mollis diam, non venenatis libero condimentum non. Sed porta efficitur ipsum in elementum<br>blandit a magna sit amet auctor.</p>
  <p class="promo-code">GET THIS CODE: <b>TAPLEDGER 0000</b></p>
</div>
<svg class="abs arrow" style="left:1083px;top:2603px" viewBox="0 0 30 46"><path d="M6 4l18 19L6 42" fill="none" stroke="#c9cde0" stroke-width="5"/></svg>
<a class="abs btn btn-light" href="#" style="left:488px;top:2753px;width:224px;height:55px;font-size:16px">VIEW ALL CODES</a>

<!-- plans -->
<h2 class="abs section-title" style="top:2926px">Plans For Everyone</h2>
<div class="abs plan" style="left:254px;top:3031px">
  <div class="price"><strong><sup>$</sup>4.99</strong><small>+ gst / month</small></div>
  <h3>Personal Plan</h3>
  <p>Provides for one keyword and one personal TapLedger.</p>
  <a class="btn btn-solid" href="#">SIGN UP</a>
</div>
<div class="abs plan" style="left:614px;top:3031px">
  <div class="price"><strong><sup>$</sup>6.99</strong><small>+ gst / month</small></div>
  <h3>Business Plan</h3>
  <p>Provides for one keyword and one personal TapLedger.</p>
  <a class="btn btn-solid" href="#">SIGN UP</a>
</div>

<!-- testimonials -->
<h2 class="abs section-title light" style="top:3575px">Our Clients Love Us!</h2>
<svg class="abs arrow" style="left:98px;top:3775px" viewBox="0 0 30 46"><path d="M24 4L6 23l18 19" fill="none" stroke="#c9cde0" stroke-width="5"/></svg>
<div class="abs quote-card">
  <span class="abs qmark" style="left:14px;top:10px">“</span>
  <span class="abs qmark" style="right:36px;top:150px">”</span>
  <p>This service gained me 10 listings for me over the past year! For me is the best and most powerful tool available<br>in the Real Estate industry. I often get caught out in social occasions, bars, restaurants, expos, the beach,<br>everywhere without a business card, but with TapLedger I can instantly have all my details sent directly to my<br>potential customers phone and most powerfully a web link directly to my profile page with all my listings.<br>I would highly recommend it to anyone.</p>
  <h3>Mara Whitfield</h3>
  <p class="role">Licensee Salesperson, Harbour Realty Limited</p>
</div>
<svg class="abs arrow" style="left:1083px;top:3775px" viewBox="0 0 30 46"><path d="M6 4l18 19L6 42" fill="none" stroke="#c9cde0" stroke-width="5"/></svg>

<!-- subscribe -->
<h2 class="abs section-title" style="top:4178px">Email Subscribe</h2>
<p class="abs subscribe-copy">Sed dapibus odio eget vestibulum ultricesliquam pharetra dolor et aliquam luctus.</p>
<div class="abs field" style="left:291px;top:4302px;width:426px;height:52px;font-size:14px;box-shadow:0 2px 8px rgba(0,0,0,.08)">Enter Email Address</div>
<a class="abs btn btn-solid" href="#" style="left:732px;top:4302px;width:175px;height:50px;font-size:16px">SUBSCRIBE</a>

<!-- footer -->
<div class="abs footer-brand"><i></i>TapLedger</div>
<p class="abs fine" style="left:75px;top:4680px">Copyright © 2020, Company Name<br>All Right reserved</p>
<p class="abs fine" style="left:75px;top:4733px">ABN: 12345678901</p>

<div class="abs foot-col" style="left:351px;top:4566px">
  <h4>Site Map</h4>
  <ul><li>Home</li><li>Partners</li><li>Benefits</li><li>Plans</li><li>Testimonials</li><li>Log in</li><li>Sign up</li></ul>
</div>
<div class="abs foot-col" style="left:588px;top:4566px">
  <h4>Postal Address</h4>
  <p>PO BOX 4120 Coral Bay QLD</p>
  <p style="display:flex;align-items:center;gap:14px"><svg width="14" height="10" viewBox="0 0 14 10"><rect width="14" height="10" fill="#d6d6d6"/><path d="M0 0l7 6 7-6" fill="none" stroke="#2b2b2b" stroke-width="1.4"/></svg>support@tapledger.example</p>
  <h4 style="margin-top:28px">Registered Address:</h4>
  <p>18 Harbour View Parade,<br>Coral Bay QLD 4217</p>
</div>
<div class="abs foot-col" style="left:885px;top:4566px">
  <h4>Follow Us</h4>
  <div class="socials"><span>Chatterbook</span><span>Chirper</span><span>Snapgrid</span></div>
  <div class="socials" style="margin-top:6px"><span>LinkLoop</span><span>ClipStream</span></div>
  <h4 style="margin-top:34px">Payment</h4>
  <div class="cards"><span></span><span></span><span></span><span></span><span></span></div>
</div>

</body>
</html>
```